Realty Group Needs Classy, Contemporary Letterhead Design

We need a letterhead design for a new realty company located in NY, USA. We buy investment properties to rehabilitate and or keep in our rental portfolio.

```html
<!DOCTYPE html>
<html lang="en">
<head>
<meta charset="utf-8">
<title>Meridian Realty Group – Letterhead</title>
<link rel="stylesheet" href="https://fonts.googleapis.com/css2?family=Arimo:wght@400;700&family=Montserrat:wght@800&family=Open+Sans:wght@400;700&family=Dancing+Script&display=swap">
<style>
  :root {
    --backdrop: #e9e9ea;
    --paper: #ffffff;
    --brand-purple: #4f2a8c;
    --swoosh-grey: #b9b9bd;
    --body-grey: #6d6d70;
    --ink-dark: #4a4a4d;
  }
  * { box-sizing: border-box; margin: 0; padding: 0; }
  html, body {
    width: 1200px; height: 795px; overflow: hidden;
    background: var(--backdrop);
  }
  .letterhead {
    position: absolute; left: 332px; top: 18px;
    width: 536px; height: 759px;
    background: var(--paper);
    box-shadow: 0 2px 10px rgba(0,0,0,0.12);
    overflow: hidden;
    font-family: "Arimo", Arial, sans-serif;
    color: var(--body-grey);
  }
  .brand {
    position: absolute; top: 46px; left: 0; width: 100%;
    display: flex; justify-content: center; align-items: center; gap: 8px;
  }
  .brand-dot { width: 10px; height: 10px; border-radius: 50%; background: var(--brand-purple); }
  .brand-name {
    font-family: "Montserrat", sans-serif; font-weight: 800;
    font-size: 22px; letter-spacing: 0.5px; color: var(--brand-purple);
  }
  .letter {
    position: absolute; top: 150px; left: 52px; width: 432px;
    font-size: 10.5px; line-height: 1.3;
  }
  .letter-date { margin-bottom: 16px; }
  .recipient { margin-bottom: 16px; font-style: normal; }
  .salutation { font-weight: 700; color: var(--ink-dark); margin-bottom: 12px; }
  .letter p.body { margin-bottom: 12px; }
  .closing {
    margin-top: 4px;
    text-align: right; font-size: 10.5px; line-height: 1.3;
  }
  .signature {
    font-family: "Dancing Script", cursive; font-size: 22px; line-height: 1.2;
    color: var(--body-grey); margin: 4px 0 2px;
  }
  .contact {
    position: absolute; right: 40px; top: 604px;
    text-align: right; font-family: "Open Sans", sans-serif;
    font-size: 9px; line-height: 1.45; color: var(--ink-dark);
  }
  .contact-company { font-weight: 700; color: var(--brand-purple); }
  .contact-web { font-weight: 700; color: var(--brand-purple); }
  .contact-line { display: flex; justify-content: flex-end; align-items: center; gap: 3px; }
  .contact-icon { width: 9px; height: 9px; }
  .footer-wave { position: absolute; left: 0; bottom: 0; width: 536px; height: 150px; }
</style>
</head>
<body>
  <main class="letterhead">
    <header class="brand">
      <span class="brand-dot"></span>
      <span class="brand-name">MERIDIAN</span>
    </header>

    <section class="letter">
      <p class="letter-date">January 12, 2021</p>
      <address class="recipient">
        Mr. John Doe<br>President<br>AA Corporation<br>111 Street Name, Suite#<br>City, State, 12345
      </address>
      <p class="salutation">Dear Mr. John,</p>
      <p class="body">Lorem Ipsum is simply dummy text of the printing and typesetting industry. Lorem Ipsum has been the industry's standard dummy text ever since the 1500s, when an unknown printer took a galley of type and scrambled it to make a type specimen book. It has survived not only five centuries, but also the leap into electronic typesetting, remaining essentially unchanged.</p>
      <p class="body">The standard chunk of Lorem Ipsum used since the 1500s is reproduced below for those interested. Sections 1.10.32 and 1.10.33 from "de Finibus Bonorum et Malorum" by Cicero are also reproduced in their exact original form, accompanied by English versions from the 1914 translation by H. Rackham.</p>
      <p class="body">Lorem Ipsum is simply dummy text of the printing and typesetting industry. Lorem Ipsum has been the industry's standard dummy text ever since the 1500s, when an unknown printer took a galley of type and scrambled it to make a type specimen book. It has survived not only five centuries, but also the leap into electronic typesetting, remaining essentially unchanged. It was popularised in the</p>

      <div class="closing">
        <p>Sincerely Your,</p>
        <p class="signature">your name</p>
        <p>Name Last Name</p>
        <p>Company Name</p>
      </div>
    </section>

    <footer class="contact">
      <p class="contact-company">Meridian Realty Group, LLC</p>
      <p>Suite 102 Street Name, State, Zip 2034, Country</p>
      <p class="contact-line">
        <svg class="contact-icon" viewBox="0 0 10 10"><circle cx="5" cy="5" r="5" fill="var(--brand-purple)"/><path d="M3.2 2.6l1 1-.5.6a3 3 0 0 0 1.9 1.9l.6-.5 1 1-.7.8A4.5 4.5 0 0 1 2.4 3.3z" fill="#fff"/></svg>
        (00) 05550 123 456
        <svg class="contact-icon" viewBox="0 0 10 10"><circle cx="5" cy="5" r="5" fill="var(--brand-purple)"/><rect x="3" y="2.5" width="4" height="5" rx=".6" fill="#fff"/></svg>
        (00) 05550 123 457
        <svg class="contact-icon" viewBox="0 0 10 10"><circle cx="5" cy="5" r="5" fill="var(--brand-purple)"/><rect x="2.5" y="3.2" width="5" height="3.6" fill="#fff"/><path d="M2.5 3.2L5 5.2 7.5 3.2" stroke="var(--brand-purple)" stroke-width=".6" fill="none"/></svg>
        hello@meridianrealty.com
      </p>
      <p class="contact-web">www.meridianrealty.com</p>
    </footer>

    <svg class="footer-wave" viewBox="0 0 536 150" preserveAspectRatio="none" aria-hidden="true">
      <path d="M0 10 C 20 90, 120 118, 536 126 L536 150 L0 150 Z" fill="var(--swoosh-grey)"/>
      <path d="M0 22 C 25 100, 140 126, 536 134 L536 150 L0 150 Z" fill="var(--brand-purple)"/>
    </svg>
  </main>
</body>
</html>
```